Market place for used airplanes/helicopters/parts

http://www.vingtorget.se needs a facelift.

# What is it
Classifieds for used airplanes/helicopters/parts/spare parts/aviation literature, for people in Scandinavia. The number of classifieds is ~120-200. They are mainly in Swedish, English, Norwegian.

It's not a glamorous or luxurious business, but more for people with a genuine interest in flying, technical things.

Similar to sites like this, but they have much more classifieds than my site
http://www.skyvendor.com/list/list.aspx?ETID=1&setype=1&catid=6
http://www.lindqvistflyg.com/planes.asp?meny=1&typ=single
https://www.hangarhub.com/cat.php?mode=listing&main=

# What I want
Design only - no code. I want a modern, maybe a bit bootstrap like, clean, simple, not flashy, web design. I want the design to be in English.

# Audience of the website
Aviation interested men, 45-65 years old, in the nordic countries (around Sweden).

# Logotype that could be used (but not necessarily)
http://www.vingtorget.se/flygplan_till_salu_large.jpg
http://www.vingtorget.se/flygplan_till_salu.eps

Reason: I decided to extend the deadline with 1 day. The reason is that I (unfortunately) managed to put the contest in the wrong category for 1 day + I want to give you all feedback (been too busy the whole day, sorry).

Hi all! 

Thanks everyone for the contributions you made. 

I will setup a poll for the designs that I like most. Will get back when I have more information. 

Thanks and have a nice weekend!
Erik

Target Market(s)

45-65 old Scandinavian men

Industry/Entity Type

Business

Requirements
Must have
• - A list with classifieds on the first page, so the visitor easily can see new classifieds.
- A classifieds should be able to have more than one photo
- A simple navigation for showing classifieds from categories like airplanes, helicopters/gyrocopters, parts, literature, misc (maybe other categories) .... but still, it's just 100-200 ads so it's not needed that much filtration.

- A placeholder/way of showing aviation news/clips. In the old design I had, it was a column to the right. It's enough to show maybe 2-5 placeholders.
- A placeholder for PlaceMint ads somewhere on the site.
Should not have
• - Carousels
- Too much clutter

```html
<!DOCTYPE html>
<html lang="en">
<head>
<meta charset="utf-8">
<title>Vingtorget – Aircraft For Sale</title>
<link href="https://fonts.googleapis.com/css2?family=Lato:wght@300;400;700;900&display=swap" rel="stylesheet">
<style>
:root{
  --blue:#0a5aa3;
  --blue-dark:#064a8a;
  --sky:#cfe6f7;
  --accent:#1aa3e8;
  --slate:#35475e;
  --page:#e9e9e9;
  --text:#555;
  --dark:#222;
  --red:#d6333a;
  --white:#fff;
}
*{box-sizing:border-box;margin:0;padding:0}
html,body{width:1082px;height:1200px;overflow:hidden}
body{background:var(--page);font-family:'Lato',sans-serif;color:var(--text);position:relative}
.site-header{position:absolute;left:0;top:0;width:1082px;height:135px;background:linear-gradient(180deg,#b9dcf4 0%,#e3f1fb 70%,#f4f9fd 100%)}
.brand{position:absolute;left:0;width:1082px;top:62px;text-align:center;font-weight:900;font-size:30px;color:var(--blue);letter-spacing:1px}
.brand-dot{display:inline-block;width:16px;height:16px;border-radius:50%;background:var(--accent);margin-right:8px;vertical-align:2px}
.social{position:absolute;left:801px;top:106px;display:flex;gap:6px}
.social span{width:20px;height:20px;border-radius:50%;background:var(--white);border:2px solid #d5e8f6}
.main-nav{position:absolute;left:0;top:135px;width:1082px;height:45px;background:var(--blue);border-top:2px solid var(--accent);border-bottom:2px solid var(--accent)}
.main-nav ul{list-style:none;position:absolute;left:171px;top:0;display:flex;height:41px}
.main-nav li{color:var(--white);font-size:14px;padding:0 9px;line-height:41px;border-right:1px solid #2a73b6;letter-spacing:-.3px}
.main-nav li:last-child{border:0}
.search{position:absolute;left:597px;top:7px;width:298px;height:30px;display:flex}
.search .field{flex:1;background:var(--white);font-size:9px;color:#aaa;line-height:30px;padding-left:19px}
.search .btn{width:37px;background:var(--accent);display:flex;align-items:center;justify-content:center}
.page-title{position:absolute;left:179px;top:208px;font-size:31px;font-weight:900;color:var(--blue);letter-spacing:-1.2px}
.welcome{position:absolute;left:180px;top:249px;font-size:13px;font-weight:300;color:var(--dark);letter-spacing:-.3px}
.welcome b{color:var(--accent);font-weight:700}
.rule{position:absolute;left:179px;top:285px;width:716px;height:2px;background:#d2d2d2}
.listing{position:absolute;left:179px;width:508px;height:237px;background:var(--white)}
.listing h2{height:40px;background:var(--slate);color:var(--white);font-size:21px;font-weight:700;line-height:40px;padding-left:24px;letter-spacing:-.8px}
.photos{position:absolute;left:22px;top:52px;display:flex;gap:1px}
.photos div{width:86px;height:70px}
.desc{position:absolute;left:22px;top:130px;width:480px;font-size:9.5px;line-height:14px;color:#666;white-space:nowrap}
.desc b{color:var(--blue);font-weight:700;margin-left:4px}
.meta{position:absolute;left:0;top:177px;width:508px;height:31px;border-top:1px solid #e3e3e3;border-bottom:1px solid #e3e3e3;display:flex;align-items:center;gap:12px;padding-left:22px;font-size:9.5px;color:var(--dark)}
.meta span{display:flex;align-items:center;gap:4px}
.meta em{font-style:normal;color:var(--blue);font-weight:700}
.date-row{position:absolute;left:22px;top:208px;width:466px;height:29px;display:flex;align-items:center;font-size:10px;font-weight:700;color:var(--blue)}
.date-row .dots{flex:1;border-top:1px dotted #ccc;margin:0 15px}
.date-row .read{background:var(--blue);color:var(--white);font-size:8px;padding:5px 7px;border-radius:2px}
.spinner{position:absolute;left:411px;top:1074px}
.box-head{height:32px;background:var(--blue);color:var(--white);font-size:14px;font-weight:700;line-height:32px;padding-left:14px;letter-spacing:-.4px}
.video{position:absolute;left:703px;top:308px;width:191px;height:159px;background:#ccc}
.video-frame{position:absolute;left:3px;top:35px;width:185px;height:121px;background:linear-gradient(135deg,#5a5a5a,#1c1c1c)}
.video-bar{position:absolute;left:0;bottom:0;width:185px;height:11px;background:#ddd}
.play{position:absolute;left:80px;top:45px}
.news{position:absolute;left:703px;top:483px;width:191px;height:237px;background:var(--white)}
.news-item{position:relative;height:68px;border-bottom:1px solid #e5e5e5}
.news-item:last-child{border:0}
.day{position:absolute;left:12px;top:10px;width:40px;height:40px;border-radius:50%;background:#e6e6e6;text-align:center;font-size:18px;font-weight:900;color:var(--dark);line-height:30px}
.day small{position:absolute;left:0;width:40px;top:26px;font-size:6px;line-height:8px;color:#777;font-weight:400}
.time{position:absolute;left:14px;top:53px;font-size:8px;font-weight:700;color:var(--dark)}
.news-text{position:absolute;left:63px;top:12px;width:122px;font-size:8px;line-height:11px;color:var(--red)}
.news-text b{display:block;color:var(--blue);margin-top:4px}
.ad{position:absolute;left:704px;width:190px;height:179px;background:var(--slate);border-radius:2px;padding:14px 0 0 18px;color:var(--white);line-height:1}
.ad .l1{font-size:26px;font-weight:700;letter-spacing:-1px}
.ad .l2{font-size:32px;font-weight:900;margin-top:3px}
.site-footer{position:absolute;left:0;top:1153px;width:1082px;height:47px;background:var(--blue);font-size:9px;color:#bcd8f2}
.site-footer .links{position:absolute;left:180px;top:19px}
.site-footer .copy{position:absolute;left:685px;top:19px}
</style>
</head>
<body>
<header class="site-header">
  <div class="brand"><span class="brand-dot"></span>VINGTORGET</div>
  <div class="social" aria-label="Social links"><span></span><span></span><span></span><span></span></div>
</header>
<nav class="main-nav">
  <ul><li>Airplanes</li><li>Helicopters / Gyrocopters</li><li>Parts</li><li>Literature</li><li>Misc</li></ul>
  <div class="search"><div class="field">Search Parts, Copters, Airplanes.......</div>
    <div class="btn"><svg width="16" height="16" viewBox="0 0 16 16"><circle cx="6.5" cy="6.5" r="4.5" fill="none" stroke="#fff" stroke-width="2.2"/><line x1="10" y1="10" x2="14.5" y2="14.5" stroke="#fff" stroke-width="2.6" stroke-linecap="round"/></svg></div></div>
</nav>
<h1 class="page-title">Aircraft For Sale - The Largest Market For Flights</h1>
<p class="welcome">Welcome Back ! Site Is Under Reconstruction / Website Is Under Reconstruction <b>Upload / Change Ad (add / Edit Your Ad)</b></p>
<div class="rule"></div>

<article class="listing" style="top:308px">
  <h2>Skarvik HX ULC</h2>
  <div class="photos">
    <div role="img" aria-label="Red aircraft propeller close-up" style="background:linear-gradient(135deg,#9b2b2b,#3d4a5a)"></div>
    <div role="img" aria-label="Red aircraft flying over landscape" style="background:linear-gradient(135deg,#8a9078,#b54040)"></div>
    <div role="img" aria-label="Red aircraft in a steep bank" style="background:linear-gradient(160deg,#c9c6c0,#8d857b)"></div>
    <div role="img" aria-label="Red aircraft inverted over hills" style="background:linear-gradient(180deg,#e4dcd6,#8f9aa8)"></div>
    <div role="img" aria-label="Aircraft in evening light" style="background:linear-gradient(135deg,#6b6b6b,#e8d6a6)"></div>
  </div>
  <p class="desc">Experimental clipped wing +9 /-6G airshow performer for sale in Norway. Two stroke Nordmot N580 fully<br>inverted system. Built in 1994, new wings in 2011. Total time 401 hours, 135 engine hours. Customized<br>pocket fighter........ <b>View More &gt;&gt;</b></p>
  <div class="meta">
    <span><svg width="12" height="12" viewBox="0 0 12 12"><polygon points="6,0 7.6,4 12,4.4 8.6,7.2 9.7,11.6 6,9.2 2.3,11.6 3.4,7.2 0,4.4 4.4,4" fill="#0a5aa3"/></svg>Aero Parts Nord, TT 222 hrs,</span>
    <span><svg width="14" height="11" viewBox="0 0 14 11"><rect x="0" y="1" width="10" height="8" rx="1" fill="none" stroke="#0a5aa3" stroke-width="1.4"/><circle cx="10" cy="6" r="3.5" fill="#0a5aa3"/></svg><em>Price :</em> 1200 SEK</span>
    <span><svg width="11" height="11" viewBox="0 0 11 11"><circle cx="5.5" cy="3" r="2.8" fill="#0a5aa3"/><path d="M0 11 Q5.5 3 11 11Z" fill="#0a5aa3"/></svg><em>Name :</em> Lars-Åke</span>
    <span><svg width="11" height="11" viewBox="0 0 11 11"><rect width="11" height="11" rx="2" fill="#0a5aa3"/><path d="M3 2.5 L4.5 2.5 L5 4.5 L4 5 Q5 7 6 7 L6.5 6 L8.5 6.5 L8.5 8 Q4 9 3 2.5Z" fill="#fff"/></svg><em>Phone :</em> 0700-118245</span>
  </div>
  <div class="date-row"><svg width="14" height="14" viewBox="0 0 14 14"><circle cx="7" cy="7" r="6" fill="none" stroke="#0a5aa3" stroke-width="1.6"/><path d="M7 3.5V7L9.5 8.5" stroke="#0a5aa3" stroke-width="1.6" fill="none"/></svg>&nbsp;Date : <span style="color:#222">&nbsp;2013-10-05 19:31:18</span><span class="dots"></span><span class="read">Read More</span></div>
</article>

<article class="listing" style="top:561px">
  <h2>Skarvik HX ULC</h2>
  <div class="photos">
    <div role="img" aria-label="Yellow aircraft on grass field" style="background:linear-gradient(160deg,#d9cfb7,#6c6a4b)"></div>
    <div role="img" aria-label="Red aircraft parked in a field" style="background:linear-gradient(135deg,#5f7a4f,#c23e36)"></div>
    <div role="img" aria-label="Yellow aircraft taxiing" style="background:linear-gradient(180deg,#a8a08a,#d8c95a)"></div>
    <div role="img" aria-label="Yellow aircraft on a beach" style="background:linear-gradient(180deg,#8fb6d6,#d7cbb0)"></div>
    <div role="img" aria-label="Cockpit instrument panel" style="background:linear-gradient(135deg,#4b5766,#9aa4ad)"></div>
  </div>
  <p class="desc">Experimental clipped wing +9 /-6G airshow performer for sale in Norway. Two stroke Nordmot N580 fully<br>inverted system. Built in 1994, new wings in 2011. Total time 401 hours, 135 engine hours. Customized<br>pocket fighter........ <b>View More &gt;&gt;</b></p>
  <div class="meta">
    <span><svg width="12" height="12" viewBox="0 0 12 12"><polygon points="6,0 7.6,4 12,4.4 8.6,7.2 9.7,11.6 6,9.2 2.3,11.6 3.4,7.2 0,4.4 4.4,4" fill="#0a5aa3"/></svg>Aero Parts Nord, TT 222 hrs,</span>
    <span><svg width="14" height="11" viewBox="0 0 14 11"><rect x="0" y="1" width="10" height="8" rx="1" fill="none" stroke="#0a5aa3" stroke-width="1.4"/><circle cx="10" cy="6" r="3.5" fill="#0a5aa3"/></svg><em>Price :</em> 1200 SEK</span>
    <span><svg width="11" height="11" viewBox="0 0 11 11"><circle cx="5.5" cy="3" r="2.8" fill="#0a5aa3"/><path d="M0 11 Q5.5 3 11 11Z" fill="#0a5aa3"/></svg><em>Name :</em> Lars-Åke</span>
    <span><svg width="11" height="11" viewBox="0 0 11 11"><rect width="11" height="11" rx="2" fill="#0a5aa3"/><path d="M3 2.5 L4.5 2.5 L5 4.5 L4 5 Q5 7 6 7 L6.5 6 L8.5 6.5 L8.5 8 Q4 9 3 2.5Z" fill="#fff"/></svg><em>Phone :</em> 0700-118245</span>
  </div>
  <div class="date-row"><svg width="14" height="14" viewBox="0 0 14 14"><circle cx="7" cy="7" r="6" fill="none" stroke="#0a5aa3" stroke-width="1.6"/><path d="M7 3.5V7L9.5 8.5" stroke="#0a5aa3" stroke-width="1.6" fill="none"/></svg>&nbsp;Date : <span style="color:#222">&nbsp;2013-10-05 19:31:18</span><span class="dots"></span><span class="read">Read More</span></div>
</article>

<article class="listing" style="top:814px">
  <h2>Skarvik HX ULC</h2>
  <div class="photos">
    <div role="img" aria-label="Red aircraft propeller close-up" style="background:linear-gradient(135deg,#9b2b2b,#3d4a5a)"></div>
    <div role="img" aria-label="Red aircraft flying over landscape" style="background:linear-gradient(135deg,#8a9078,#b54040)"></div>
    <div role="img" aria-label="Red aircraft in a steep bank" style="background:linear-gradient(160deg,#c9c6c0,#8d857b)"></div>
    <div role="img" aria-label="Red aircraft inverted over hills" style="background:linear-gradient(180deg,#e4dcd6,#8f9aa8)"></div>
    <div role="img" aria-label="Aircraft in evening light" style="background:linear-gradient(135deg,#6b6b6b,#e8d6a6)"></div>
  </div>
  <p class="desc">Experimental clipped wing +9 /-6G airshow performer for sale in Norway. Two stroke Nordmot N580 fully<br>inverted system. Built in 1994, new wings in 2011. Total time 401 hours, 135 engine hours. Customized<br>pocket fighter........ <b>View More &gt;&gt;</b></p>
  <div class="meta">
    <span><svg width="12" height="12" viewBox="0 0 12 12"><polygon points="6,0 7.6,4 12,4.4 8.6,7.2 9.7,11.6 6,9.2 2.3,11.6 3.4,7.2 0,4.4 4.4,4" fill="#0a5aa3"/></svg>Aero Parts Nord, TT 222 hrs,</span>
    <span><svg width="14" height="11" viewBox="0 0 14 11"><rect x="0" y="1" width="10" height="8" rx="1" fill="none" stroke="#0a5aa3" stroke-width="1.4"/><circle cx="10" cy="6" r="3.5" fill="#0a5aa3"/></svg><em>Price :</em> 1200 SEK</span>
    <span><svg width="11" height="11" viewBox="0 0 11 11"><circle cx="5.5" cy="3" r="2.8" fill="#0a5aa3"/><path d="M0 11 Q5.5 3 11 11Z" fill="#0a5aa3"/></svg><em>Name :</em> Lars-Åke</span>
    <span><svg width="11" height="11" viewBox="0 0 11 11"><rect width="11" height="11" rx="2" fill="#0a5aa3"/><path d="M3 2.5 L4.5 2.5 L5 4.5 L4 5 Q5 7 6 7 L6.5 6 L8.5 6.5 L8.5 8 Q4 9 3 2.5Z" fill="#fff"/></svg><em>Phone :</em> 0700-118245</span>
  </div>
  <div class="date-row"><svg width="14" height="14" viewBox="0 0 14 14"><circle cx="7" cy="7" r="6" fill="none" stroke="#0a5aa3" stroke-width="1.6"/><path d="M7 3.5V7L9.5 8.5" stroke="#0a5aa3" stroke-width="1.6" fill="none"/></svg>&nbsp;Date : <span style="color:#222">&nbsp;2013-10-05 19:31:18</span><span class="dots"></span><span class="read">Read More</span></div>
</article>

<svg class="spinner" width="62" height="62" viewBox="0 0 62 62" aria-label="Loading">
  <g fill="none" stroke-width="12">
    <path d="M31 6 A25 25 0 0 1 53 19" stroke="#d8d8d8"/>
    <path d="M55 25 A25 25 0 0 1 50 47" stroke="#a5a5a5"/>
    <path d="M45 52 A25 25 0 0 1 22 54" stroke="#8d8d8d"/>
    <path d="M16 51 A25 25 0 0 1 7 31" stroke="#9a9a9a"/>
    <path d="M8 24 A25 25 0 0 1 24 7" stroke="#c4c4c4"/>
  </g>
</svg>

<aside class="video">
  <div class="box-head">See Our Video</div>
  <div class="video-frame" role="img" aria-label="Video still of a vintage aircraft">
    <svg class="play" width="26" height="26" viewBox="0 0 26 26"><circle cx="13" cy="13" r="12" fill="#ddd" stroke="#555"/><polygon points="10,7 19,13 10,19" fill="#333"/></svg>
    <div class="video-bar"></div>
  </div>
</aside>

<aside class="news">
  <div class="box-head">Latest News</div>
  <div class="news-item"><div class="day">18<small>AUG</small></div><div class="time">5:00 <span style="font-weight:400;color:#777">PM</span></div><p class="news-text">Lorem Ipsum Dolor Sit Amet, Consectetuer Adipiscing Elit Dolor Sit Amet, Consectetuer<b>View More &gt;&gt;</b></p></div>
  <div class="news-item"><div class="day">17<small>AUG</small></div><div class="time">5:00 <span style="font-weight:400;color:#777">PM</span></div><p class="news-text">Lorem Ipsum Dolor Sit Amet, Consectetuer Adipiscing Elit Dolor Sit Amet, Consectetuer<b>View More &gt;&gt;</b></p></div>
  <div class="news-item"><div class="day">16<small>AUG</small></div><div class="time">5:00 <span style="font-weight:400;color:#777">PM</span></div><p class="news-text">Lorem Ipsum Dolor Sit Amet, Consectetuer Adipiscing Elit Dolor Sit Amet, Consectetuer<b>View More &gt;&gt;</b></p></div>
</aside>

<aside class="ad" style="top:737px"><div class="l1">Advertise Your</div><div class="l2">BUSINESS<br>HERE...</div></aside>
<aside class="ad" style="top:931px"><div class="l1">Advertise Your</div><div class="l2">BUSINESS<br>HERE...</div></aside>

<footer class="site-footer">
  <div class="links">HOME | &nbsp;SITEMAP | &nbsp;CAREERS | &nbsp;CONTACT US | PRIVACY POLICY</div>
  <div class="copy">COPYRIGHT © 2013 VINGTORGET ALL RIGHTS RESERVS</div>
</footer>
</body>
</html>
```